Business Card Design Project

- makeup artist business card

- original and creative

- Elegant design

- Feel free to come out with cool designs but stick to being elegant and attractive

- Design relates to makeup

- includes name, occupation, contact numbers, email, website

- regular size business card

- round corner card

- double sided

- on 1 side it should just have the website name in the center " moonveilstudio.net "

Industry/Entity Type

Business

Requirements
Must have
• Delia Marsh
Makeup Artist
USA: +1 (415)772-0461
Singapore: +65 82307915
deliamarsh@moonveilstudio.net
www.moonveilstudio.net
Should not have
• nothing cartoon looking.
Pictures of makeup being grab from the internet.. Examples: eyes or lips.

```html
<!DOCTYPE html>
<html lang="en">
<head>
<meta charset="utf-8">
<title>Delia Marsh – Makeup Artist Business Card</title>
<link rel="stylesheet" href="https://fonts.googleapis.com/css2?family=Tinos:wght@400;700&display=swap">
<style>
  :root {
    --page: #e9e7ec;
    --panel: #dcd6e0;
    --band: #2f1a55;
    --name-band: #4756b5;
    --pink-name: #c58bd6;
    --white: #ffffff;
    --ink: #111111;
    --stripe-blue: #4756b5;
    --stripe-red: #e32a2e;
    --stripe-orange: #f59a22;
    --stripe-green: #9cc93a;
    --stripe-purple: #8a5fb5;
    --email-ink: #7a3fa8;
    --web-ink: #3b49a8;
  }
  * { margin: 0; padding: 0; box-sizing: border-box; }
  html, body { width: 1067px; height: 1200px; overflow: hidden; }
  body {
    background: var(--page);
    font-family: "Tinos", "Times New Roman", serif;
    position: relative;
  }
  .card {
    position: absolute;
    left: 83px;
    width: 900px;
    height: 514px;
    border-radius: 38px;
    overflow: hidden;
    background: var(--panel);
    box-shadow: 0 8px 24px rgba(40, 30, 60, 0.22);
  }
  .card--front { top: 50px; }
  .card--back { top: 636px; }
  .photo {
    position: absolute;
    left: 0; top: 0;
    width: 410px; height: 100%;
    background:
      radial-gradient(ellipse at 62% 22%, #4fc7b0 0%, #3a9fcf 18%, rgba(230,170,150,0) 40%),
      radial-gradient(ellipse at 10% 60%, #d9b36c 0%, rgba(217,179,108,0) 45%),
      linear-gradient(180deg, #efb9a0 0%, #e7a58d 60%, #d89078 100%);
  }
  .accent-band {
    position: absolute;
    top: 0; left: 405px;
    width: 90px; height: 100%;
    background: var(--band);
  }
  .panel {
    position: absolute;
    top: 0; left: 495px; right: 0; height: 100%;
    background: linear-gradient(160deg, #e3dee7 0%, var(--panel) 100%);
  }
  .name-band {
    position: absolute;
    left: 488px; top: 152px;
    width: 372px; height: 108px;
    background: var(--name-band);
    padding: 18px 0 0 16px;
  }
  .name {
    font-size: 38px;
    font-weight: 700;
    color: var(--white);
    line-height: 1;
  }
  .name .surname { color: var(--pink-name); }
  .role {
    font-size: 28px;
    color: var(--white);
    margin: 6px 0 0 52px;
    line-height: 1;
  }
  .contacts {
    position: absolute;
    left: 28px; top: 270px;
    width: 387px;
    list-style: none;
  }
  .contacts li {
    height: 38px;
    line-height: 38px;
    padding-left: 8px;
    font-size: 23px;
    white-space: nowrap;
  }
  .contacts .phone-us { background: var(--stripe-blue); color: var(--white); }
  .contacts .phone-sg { background: var(--stripe-red); color: var(--white); }
  .contacts .email { background: var(--stripe-orange); color: var(--email-ink); font-size: 21px; }
  .contacts .web { background: var(--stripe-green); color: var(--web-ink); }
  .contacts .spacer { background: var(--stripe-purple); height: 44px; }
  .site {
    position: absolute;
    left: 495px; right: 0; top: 218px;
    text-align: center;
    font-size: 38px;
    color: var(--ink);
  }
</style>
</head>
<body>
  <section class="card card--front">
    <div class="photo" role="img" aria-label="Close-up beauty photograph of a model with bright teal and green eye makeup and blonde curls"></div>
    <div class="accent-band"></div>
    <div class="panel" role="img" aria-label="Soft lilac damask pattern background"></div>
    <div class="name-band">
      <div class="name">Delia <span class="surname">Marsh</span></div>
      <div class="role">Makeup Artist</div>
    </div>
    <ul class="contacts">
      <li class="phone-us">Phone USA: +1 (415)772-0461</li>
      <li class="phone-sg">PhoneSingapore: +65 82307915</li>
      <li class="email">deliamarsh@moonveilstudio.net</li>
      <li class="web">www.moonveilstudio.net</li>
      <li class="spacer"></li>
    </ul>
  </section>

  <section class="card card--back">
    <div class="photo" role="img" aria-label="Beauty photograph of a model with colourful eye makeup and magenta lips"></div>
    <div class="accent-band"></div>
    <div class="panel" role="img" aria-label="Soft lilac damask pattern background"></div>
    <p class="site">www.moonveilstudio.net</p>
  </section>
</body>
</html>
```